Counseling Practice Business Card

I need a professional looking business card incorporating my new logo that was just completed. Card needs to incorporate my name and title, description of my specialty, my address, my phone number, my fax number, my email and my website URL. I need to be able to choose design on/with different paper colors and textures.
I do not have a lot of business card ideas so I am open to anything but I want bold,sharp, clear card without additional designs other than my logo (see attached file info). I am open to different color backgrounds or paper colors including black. I do not like traditional brackets around area codes in phone number or dashes between numbers in phone number. Am open to other ways of presenting including periods between numbers as appropriate. I do not know enough to know what I like yet but I want card to coordinate and work together with my logo. My practice emphasizes natural mental health interventions so any use of color (with background paper color or the blue and green in my logo) that elicits nature is nice. In addition to black, any natural brown or wood looking background might be desirable also. Most of the offerings so far look very similar and boring.

Target Market(s)

Potential therapy clients and other professionals

Contact Information for Business Card

Card information:
Gerald M. Whitcombe, Ph.D.
Licensed Clinical Psychologist
Integrative Health Coach
4812 Marlowe Ridge Blvd SE
Suite 310
Duluth, GA 30096
(770) 415-2983 phone
(770) 581-4096 fax
drgeraldwhitcombe@quillmarsh.net
brightfernwellness.net

Font styles to use
Serif
Sans Serif
Other font styles liked:
• anything that you think looks crisp, clear and easily readable

Requirements
Must have
• Any color used should coordinate with my logo design (see attached files).
• Card should be printed horizontally so top and bottom are longest sides of rectangle.
• Background color or paper color should complement and highlight logo. Do not like a white background. black, grey, brown or any color my logo would blend well with.
Nice to have
• I would like designer to utilize color to highlight letters/name or phone-fax-web symbols.
• Bottom edge of card could be highlighted if appropriate to an idea.
Should not have
• I would NOT want the card to have a pure white background at all.
• No clear cards.
• Cards should be oriented with long sides on bottom and top, NOT sides. DO NOT LIKE THIS THIN TALL ORIENTATION.

```html
<!DOCTYPE html>
<html lang="en">
<head>
<meta charset="utf-8">
<title>Brightfern Wellness – Business Card</title>
<link rel="stylesheet" href="https://fonts.googleapis.com/css2?family=Open+Sans:wght@400;600&display=swap">
<style>
  :root {
    --backdrop: #999999;
    --card-light: #f2f4ee;
    --brand-blue: #2772b5;
    --brand-green: #1f6b34;
    --text-dark: #333333;
    --text-grey: #555555;
    --rule: #d6d9d2;
    --on-blue: #ffffff;
  }
  * { margin: 0; padding: 0; box-sizing: border-box; }
  html, body {
    width: 1200px; height: 900px; overflow: hidden;
    background: var(--backdrop);
    font-family: "Open Sans", Arial, sans-serif;
  }
  .stage { position: relative; width: 1200px; height: 900px; }

  .card {
    position: absolute;
    width: 477px; height: 294px;
    box-shadow: 2px 3px 5px rgba(0,0,0,0.45);
  }
  .card-front {
    left: 120px; top: 275px;
    background: var(--card-light);
    border-radius: 0 50px 0 50px;
  }
  .card-back {
    left: 607px; top: 273px;
    background: var(--brand-blue);
    border-radius: 50px 0 50px 0;
    display: flex; align-items: center; justify-content: center;
  }

  .brand {
    display: flex; align-items: center; gap: 10px;
    font-family: "Open Sans", Arial, sans-serif;
    font-weight: 600; white-space: nowrap;
  }
  .brand-dot { border-radius: 50%; flex: none; }
  .card-front .brand {
    position: absolute; right: 27px; top: 66px;
    font-size: 27px; color: var(--brand-blue);
  }
  .card-front .brand-dot { width: 18px; height: 18px; background: var(--brand-blue); }
  .card-back .brand { font-size: 38px; color: var(--on-blue); margin-top: -2px; }
  .card-back .brand-dot { width: 24px; height: 24px; background: var(--on-blue); }

  .holder { position: absolute; left: 28px; top: 151px; }
  .holder-name {
    font-size: 14.5px; font-weight: 600; letter-spacing: 0.3px;
    color: var(--brand-blue); text-transform: uppercase; line-height: 20px;
  }
  .holder-name .surname { color: var(--brand-green); }
  .holder-title { font-size: 12.5px; color: var(--text-dark); line-height: 18px; }

  .divider {
    position: absolute; left: 28px; top: 193px;
    width: 422px; height: 1px; background: var(--rule);
  }

  .contact-list {
    position: absolute; left: 28px; top: 202px;
    list-style: none; font-size: 12.5px; color: var(--text-dark); line-height: 17px;
  }
  .contact-list li { display: flex; align-items: center; gap: 4px; }
  .contact-list svg { width: 10px; height: 10px; fill: var(--brand-blue); flex: none; }

  .address {
    position: absolute; right: 27px; top: 236px;
    text-align: right; font-size: 12.5px; color: var(--text-grey); line-height: 17px;
    font-style: normal;
  }
</style>
</head>
<body>
<main class="stage">
  <section class="card card-front" aria-label="Card front">
    <div class="brand"><span class="brand-dot"></span>Brightfern Wellness</div>

    <div class="holder">
      <p class="holder-name">Gerald M. <span class="surname">Whitcombe</span>, Ph.D.</p>
      <p class="holder-title">Licensed Clinical Psychologist /Integrative Health Coach</p>
    </div>
    <div class="divider"></div>

    <ul class="contact-list">
      <li>
        <svg viewBox="0 0 10 10" aria-hidden="true"><path d="M1 3.5C1 2 2.5 1.5 5 1.5S9 2 9 3.5L7.3 4.2 6.6 3.2H3.4L2.7 4.2Z"/><rect x="2.2" y="5" width="5.6" height="3.6" rx="0.6"/></svg>
        770. 415.2983
      </li>
      <li>
        <svg viewBox="0 0 10 10" aria-hidden="true"><rect x="2.5" y="0.8" width="5" height="2.6"/><rect x="0.8" y="3.6" width="8.4" height="3.8" rx="0.6"/><rect x="2.5" y="6.4" width="5" height="2.8"/></svg>
        770. 581.4096
      </li>
      <li>
        <svg viewBox="0 0 10 10" aria-hidden="true"><rect x="0.6" y="2" width="8.8" height="6.2"/><path d="M0.6 2 5 5.6 9.4 2" fill="none" stroke="#f2f4ee" stroke-width="0.9"/></svg>
        drgeraldwhitcombe@quillmarsh.net
      </li>
      <li>
        <svg viewBox="0 0 10 10" aria-hidden="true"><circle cx="5" cy="5" r="4.4"/><path d="M0.8 5h8.4M5 0.8c-2.2 2.4-2.2 6 0 8.4M5 0.8c2.2 2.4 2.2 6 0 8.4" fill="none" stroke="#f2f4ee" stroke-width="0.7"/></svg>
        brightfernwellness.net
      </li>
    </ul>

    <address class="address">
      4812 Marlowe Ridge Blvd SE<br>
      Suite 310 Duluth, GA 30096
    </address>
  </section>

  <section class="card card-back" aria-label="Card back">
    <div class="brand"><span class="brand-dot"></span>Brightfern Wellness</div>
  </section>
</main>
</body>
</html>
```